New, modern business card for growing audiology practice

We need a new business card for our audiology practice. Our logo and website have recently changed (more modern) and we want our business cards to reflect this change.
We conduct hearing tests, perform earwax removals, and fit & dispense hearing aids to our patients. We are a family owned practice in which the owner is the one who works directly with the patient. I have attached logos in various formats to use, as well as two ideas I found on this website; as well as a scanned copy of our current logo. Good luck!

Industry/Entity Type

Business

Contact Information for Business Card

Company name: Tolvera Hearing Center
Provider name: Peter Wolstenby, Au.D. F/NSB
Phone number: (440) 683-5127
Address: 837 W. Lindell Ave. Brenmoor Falls, OH 44157
email: tolverahearing@postvane.com
website: tolverahearing.com

Colors
000000
aaaaaa
dbdbdb
cacaca
9bcb3c
afd23c
cadf82
b1b1b1

Requirements
Must have
• My card must include information in the "details" section. In the attached images, I found a few that I liked and I would like to model after - "brisky bouncin'" and "Sound Method Center".
• Must be horizontal.
• Must include logos provided. I uploaded them in various file formats and various ways.
• Must match logo font, if possible, if not, please get as close as you can.
Nice to have
• I really like the idea of having a color on one side with just the logo and company name and the contact information and provider name on the other side. I also really like the idea of having the main color dominating on the logo/company side with accent of that same color on the contact side of the card.
Should not have
• Must not be vertical.

```html
<!DOCTYPE html>
<html lang="en">
<head>
<meta charset="utf-8">
<title>Tolvera Hearing Center – Business Card</title>
<link rel="stylesheet" href="https://fonts.googleapis.com/css2?family=Roboto:wght@400;500&family=Roboto+Condensed:wght@700&display=swap">
<style>
  :root {
    --backdrop: #e7e4df;
    --card-white: #f4f4f3;
    --card-black: #000000;
    --brand-green: #77a83d;
    --text-dark: #111111;
    --text-grey: #555555;
    --text-light: #ffffff;
  }
  * { margin: 0; padding: 0; box-sizing: border-box; }
  html, body {
    width: 1200px; height: 960px; overflow: hidden;
    background: var(--backdrop);
  }
  .canvas { position: relative; width: 1200px; height: 960px; }

  .card {
    position: absolute; width: 600px; height: 343px; overflow: hidden;
    box-shadow: 0 3px 6px rgba(0,0,0,.35);
  }

  /* Front: contact side */
  .card--front {
    left: 314px; top: 113px;
    background: var(--card-white);
    font-family: "Roboto", Arial, sans-serif;
  }
  .front-band {
    position: absolute; right: 0; top: 0; width: 150px; height: 100%;
    background: linear-gradient(to right, rgba(0,0,0,0) 0%, rgba(0,0,0,.55) 45%, var(--card-black) 70%);
  }
  .provider { position: absolute; left: 24px; top: 162px; }
  .provider-name {
    font-family: "Roboto Condensed", "Arial Narrow", sans-serif;
    font-weight: 700; font-size: 21px; color: var(--brand-green);
    letter-spacing: .2px; line-height: 24px;
  }
  .provider-title {
    font-weight: 500; font-size: 15px; color: var(--text-dark);
    line-height: 20px; margin-top: 1px;
  }
  .address {
    position: absolute; left: 24px; top: 217px;
    font-style: normal;
    font-size: 14px; line-height: 18px; color: var(--text-grey);
  }
  .contact-list {
    position: absolute; left: 24px; top: 264px; list-style: none;
    font-size: 14px; line-height: 19.5px; color: var(--text-grey);
  }
  .contact-list li { display: flex; align-items: center; gap: 8px; }
  .contact-icon { width: 14px; height: 14px; flex: none; fill: var(--brand-green); }

  /* Back: brand side */
  .card--back {
    left: 311px; top: 472px;
    background: var(--card-black);
    font-family: "Roboto", Arial, sans-serif;
  }
  .brand {
    position: absolute; left: 0; right: 0; top: 156px;
    display: flex; justify-content: center; align-items: center; gap: 12px;
  }
  .brand-dot { width: 18px; height: 18px; border-radius: 50%; background: var(--brand-green); }
  .brand-name {
    font-weight: 400; font-size: 27px; letter-spacing: .5px;
    color: var(--text-light); text-transform: uppercase;
  }
  .back-web {
    position: absolute; left: 0; right: 0; top: 287px; text-align: center;
    font-size: 14px; letter-spacing: 4px; color: var(--text-light);
  }
  .back-web .domain { color: var(--brand-green); }
</style>
</head>
<body>
<main class="canvas">

  <section class="card card--front" aria-label="Contact side">
    <div class="front-band"></div>
    <div class="provider">
      <h1 class="provider-name">PETER WOLSTENBY</h1>
      <p class="provider-title">AU.D. F/NSB</p>
    </div>
    <address class="address">
      837 W. Lindell Ave.<br>
      Brenmoor Falls, OH 44157
    </address>
    <ul class="contact-list">
      <li>
        <svg class="contact-icon" viewBox="0 0 16 16" aria-hidden="true"><path d="M3.6 1.2 6 3.6 4.7 5.4c.9 2 2.6 3.8 4.7 4.8l1.7-1.4 2.5 2.3-1.5 2.4C7.3 13.4 2.4 8.6 1.2 3.1Z"/></svg>
        (440) 683-5127
      </li>
      <li>
        <svg class="contact-icon" viewBox="0 0 16 16" aria-hidden="true"><path d="M1 3.5h14v1L8 9 1 4.5Zm0 2.6 7 4.4 7-4.4V13H1Z"/></svg>
        tolverahearing@postvane.com
      </li>
      <li>
        <svg class="contact-icon" viewBox="0 0 16 16" aria-hidden="true"><circle cx="8" cy="8" r="7"/><path d="M1 8h14M8 1c2.4 2.2 2.4 11.8 0 14M8 1C5.6 3.2 5.6 12.8 8 15" stroke="#f4f4f3" stroke-width="1.1" fill="none"/></svg>
        tolverahearing.com
      </li>
    </ul>
  </section>

  <section class="card card--back" aria-label="Brand side">
    <div class="brand">
      <span class="brand-dot" aria-hidden="true"></span>
      <span class="brand-name">Tolvera Hearing Center</span>
    </div>
    <p class="back-web">www.<span class="domain">tolverahearing</span>.com</p>
  </section>

</main>
</body>
</html>
```